Business Cards for new orthopaedic surgery practice

My husband and I are starting our own orthopaedic surgery practice. We are looking for a business card that is uniform, but one will have my name/title and the other will have his. You can just create one design with my name on it for now. But when I choose your design as the winning design I will ask that you add another copy with his name/title.

We are looking for classy, simple, elite all in one. We like dark blues/a little gold/yellow. Something that goes with our logo. We want our logo incorporated. Here is all the info you need:
Business name: RV Bone & Vitality Center
Location: 38517 North Willowmere Ave
Cedar Bend, FL 33920
Phone: 954-218-4063
Fax: 954-582-7341
Email: info@myrvbonecare.example

Names: Lydia Vance, M.D.
Board Certified Hand and Upper Extremity Surgeon

Ebo Dansu, M.D.
Board Certified Hip & Knee Replacement/General Orthopaedic Surgeon

Can decide what you want to put on the back. Maybe a slogan:
Rooted in Care. Focused on You

I am just going to upload our logo. The only thing is if we select you as the winning design, the location, and phone numbers may change. We will need your help to update that once fully solidified.

Industry/Entity Type

Medical

Contact Information for Business Card

Colors
0054AA
0677BA
7BADD7
CADEEF
E8F1F8
0094D4
00A9DD
6FCCEA
C7EBF8
E9F6FB

Requirements
Must have
• class, appeal,
Should not have
• We want to air on the side of masculine if we are looking at masculine vs. feminine feel. But we still want it classy, sophisticated, and something we will love

```html
<!DOCTYPE html>
<html lang="en">
<head>
<meta charset="utf-8">
<title>RV Bone &amp; Vitality Center — Business Card</title>
<link rel="stylesheet" href="https://fonts.googleapis.com/css2?family=Montserrat:wght@400;500;700&display=swap">
<style>
  :root {
    --navy: #1c2a52;
    --gold: #c59d5a;
    --ink: #1a1f33;
    --paper: #ffffff;
    --stage: #3a3a3c;
  }
  * { margin: 0; padding: 0; box-sizing: border-box; }
  html, body { width: 1200px; height: 875px; overflow: hidden; }
  body {
    background: var(--stage);
    font-family: "Montserrat", sans-serif;
    position: relative;
  }
  .card {
    position: absolute;
    width: 620px;
    height: 354px;
    border-radius: 22px;
    overflow: hidden;
  }
  .card--front { left: 60px; top: 60px; background: var(--navy); }
  .card--back { left: 520px; top: 461px; background: var(--paper); }

  .brand {
    position: absolute;
    display: flex;
    align-items: center;
    gap: 12px;
    font-weight: 700;
    text-align: left;
    line-height: 1.25;
  }
  .brand__dot { flex: none; border-radius: 50%; background: var(--gold); }
  .card--front .brand {
    left: 50%; top: 50%; transform: translate(-50%, -50%);
    color: var(--paper); font-size: 30px; width: 400px;
  }
  .card--front .brand__dot { width: 34px; height: 34px; }
  .card--back .brand {
    left: 36px; top: 108px; width: 210px;
    color: var(--navy); font-size: 19px;
  }
  .card--back .brand__dot { width: 22px; height: 22px; }

  .divider {
    position: absolute; left: 262px; top: 64px;
    width: 1px; height: 160px; background: var(--ink);
  }
  .details { position: absolute; left: 282px; top: 62px; color: var(--ink); }
  .details__name { font-size: 22px; font-weight: 700; color: var(--navy); }
  .details__cred { color: var(--gold); }
  .details__title, .details__address {
    font-size: 12.5px; font-weight: 500; line-height: 1.35;
  }
  .details__title { margin-top: 2px; }
  .details__address { margin-top: 12px; }
  .contacts { list-style: none; margin-top: 8px; font-size: 12.5px; font-weight: 500; }
  .contacts li { display: flex; align-items: center; gap: 8px; line-height: 1.5; }
  .contacts svg { width: 11px; height: 11px; fill: var(--gold); flex: none; }

  .bands { position: absolute; left: 0; bottom: 0; width: 620px; height: 60px; }
</style>
</head>
<body>
  <section class="card card--front" aria-label="Card front">
    <div class="brand">
      <span class="brand__dot"></span>
      <span class="brand__name">RV Bone &amp; Vitality Center</span>
    </div>
  </section>

  <section class="card card--back" aria-label="Card back">
    <div class="brand">
      <span class="brand__dot"></span>
      <span class="brand__name">RV Bone &amp; Vitality Center</span>
    </div>
    <div class="divider"></div>
    <div class="details">
      <h1 class="details__name">Lydia Vance, <span class="details__cred">M.D.</span></h1>
      <p class="details__title">Board Certified Hand and<br>Upper Extremity Surgeon</p>
      <p class="details__address">38517 North Willowmere Ave<br>Cedar Bend, FL 33920</p>
      <ul class="contacts">
        <li>
          <svg viewBox="0 0 12 12"><path d="M2.5 1h2l1 3-1.3 1a6 6 0 0 0 2.8 2.8l1-1.3 3 1v2a1.5 1.5 0 0 1-1.5 1.5A9.5 9.5 0 0 1 1 2.5 1.5 1.5 0 0 1 2.5 1z"/></svg>
          954-218-4063
        </li>
        <li>
          <svg viewBox="0 0 12 12"><rect x="3" y="1" width="6" height="3"/><rect x="1" y="4.5" width="10" height="4.5" rx="1"/><rect x="3" y="7.5" width="6" height="3.5"/></svg>
          954-582-7341
        </li>
        <li>
          <svg viewBox="0 0 12 12"><path d="M1 2.5h10v7H1z M1 2.5l5 4 5-4" fill="none" stroke="#c59d5a" stroke-width="1.4"/></svg>
          info@myrvbonecare.example
        </li>
      </ul>
    </div>
    <svg class="bands" viewBox="0 0 620 60" preserveAspectRatio="none" aria-hidden="true">
      <polygon points="0,34 400,34 388,60 0,60" fill="var(--navy)"/>
      <polygon points="412,34 620,34 620,44 405,44" fill="var(--gold)"/>
    </svg>
  </section>
</body>
</html>
```